Flat Belly Design Graphics for Social

I want to create 9 social media graphics (new Instagram size 4:5 (1080 x 1350 pixels) focusing on our Flat Belly Graphics, using the pics attached. Use the attached pics, NO RANDOM STOCK PHOTOGRAPHY. For the color scheme of the graphics, the color palette is attached. YOU MUST POST ALL 9 GRAPHICS IN ONE ENTRY.
Using the 3 titles below, create one set of graphics. 1) with all text, then for the others, use the pictures as detailed below in IMPORTANT:
1. Ten-Week Bright Morning Reboot
2. The Quick Garden Kitchen Menu Guide
3. Studio Habits for Lasting Energy Past Midlife - Zero Gym Needed
IMPORTANT:
Only use RK Pic 1 and RK Pic 2 with the title, Ten-Week Bright Morning Reboot
Only use meal plan1 and meal plan2 pics with the title, Quick Garden Kitchen Menu Guide
Only use studio habits 1 and studio habits 2 pics with the title, Studio Habits for Lasting Energy Past Midlife - Zero Gym Needed
women over 40

```html
<!DOCTYPE html>
<html lang="en">
<head>
<meta charset="utf-8">
<title>Social Graphics Set – Garden Kitchen, Studio Habits, Morning Reboot</title>
<link rel="stylesheet" href="https://fonts.googleapis.com/css2?family=Oswald:wght@500;700&family=Yellowtail&display=swap">
<style>
  :root{
    --board:#575757;
    --forest:#2e4a48;
    --forest-glass:rgba(46,74,72,.88);
    --rose:#e896b0;
    --blush:#fce4ea;
    --blush-deep:#e597b0;
    --sky:#6fc6d8;
    --walnut:#6b4530;
    --produce-a:#b8452f;
    --produce-b:#5d7a3a;
  }
  *{margin:0;padding:0;box-sizing:border-box}
  html,body{width:967px;height:1200px;overflow:hidden;background:var(--board)}
  .board{position:relative;width:967px;height:1200px;background:var(--board);font-family:"Oswald",sans-serif;font-weight:700;text-transform:uppercase;}
  .tile{position:absolute;width:295px;height:368px;overflow:hidden}
  .col-1{left:12px}.col-2{left:335px}.col-3{left:658px}
  .row-1{top:8px}.row-2{top:415px}.row-3{top:818px}

  .stack{position:absolute;display:flex;flex-direction:column;line-height:.98;letter-spacing:-.2px}
  .center{align-items:center;text-align:center}
  .script{font-family:"Yellowtail",cursive;font-weight:400;text-transform:none;line-height:1}
  .c-rose{color:var(--rose)}.c-blush{color:var(--blush)}.c-forest{color:var(--forest)}

  .bg-forest{background:var(--forest)}
  .bg-gradient{background:linear-gradient(180deg,var(--blush) 0%,#f7d3dd 55%,var(--blush-deep) 100%)}
  .bg-soft{background:linear-gradient(180deg,var(--blush) 0%,#fff3f6 60%,#fbe3ea 100%)}

  .photo{position:absolute;inset:0}
  .photo-produce{background:radial-gradient(circle at 30% 30%,#e5a15a 0,transparent 40%),radial-gradient(circle at 70% 80%,#c53a2a 0,transparent 45%),linear-gradient(135deg,var(--produce-a),#7a4a2e 45%,var(--produce-b))}
  .photo-friends{background:linear-gradient(180deg,#e9e7e4 0%,#c7a893 45%,#f2f0ee 100%)}
  .photo-sky{background:linear-gradient(90deg,var(--sky) 0%,#c9a89a 40%,var(--sky) 100%)}
  .photo-kitchen{background:linear-gradient(180deg,var(--walnut) 0%,#9a6a4d 45%,#c9a488 100%)}
  .figure{position:absolute;background:linear-gradient(180deg,#6a4a3c 0%,#ece7e4 45%,#2a2a2a 100%);border-radius:60px 60px 0 0}

  .panel{position:absolute}
</style>
</head>
<body>
<main class="board">

  <!-- Garden kitchen: type only -->
  <section class="tile col-1 row-1 bg-forest">
    <div class="stack" style="left:34px;top:34px;">
      <span class="c-rose" style="font-size:32px">The Quick</span>
      <span class="c-rose" style="font-size:31px">Garden Kitchen</span>
      <span class="c-blush" style="font-size:98px;line-height:1">Menu</span>
      <span class="c-blush" style="font-size:88px;line-height:1">Guide</span>
    </div>
  </section>

  <!-- Garden kitchen: produce frame, side panel -->
  <section class="tile col-2 row-1">
    <div class="photo photo-produce" role="img" aria-label="Overhead spread of fresh produce, salmon, eggs and lentils on a wooden table"></div>
    <div class="panel" style="left:108px;top:66px;width:187px;height:236px;background:var(--forest-glass)"></div>
    <div class="stack" style="left:128px;top:78px;">
      <span class="c-blush" style="font-size:21px">The Quick</span>
      <span class="c-blush" style="font-size:20px">Garden Kitchen</span>
      <span class="c-rose" style="font-size:64px;line-height:1">Menu</span>
      <span class="c-rose" style="font-size:58px;line-height:1">Guide</span>
    </div>
  </section>

  <!-- Garden kitchen: produce frame, centre column -->
  <section class="tile col-3 row-1">
    <div class="photo photo-produce" role="img" aria-label="Fresh vegetables, fruit, salmon and legumes arranged around the edges"></div>
    <div class="panel bg-forest" style="left:58px;top:0;width:178px;height:368px"></div>
    <div class="stack center" style="left:58px;top:62px;width:178px">
      <span class="c-blush" style="font-size:34px">The Quick</span>
      <span class="c-blush" style="font-size:44px">Garden</span>
      <span class="c-blush" style="font-size:31px">Kitchen</span>
      <span class="c-rose" style="font-size:64px;line-height:1">Menu</span>
      <span class="c-rose" style="font-size:60px;line-height:1">Guide</span>
    </div>
  </section>

  <!-- Studio habits: type only -->
  <section class="tile col-1 row-2 bg-gradient">
    <div class="stack center" style="left:0;top:22px;width:295px">
      <span class="c-rose" style="font-size:42px">Studio</span>
      <span class="c-rose" style="font-size:42px">Habits</span>
      <span class="c-forest" style="font-size:33px">For Lasting</span>
      <span class="c-forest" style="font-size:60px">Energy</span>
      <span class="c-forest script" style="font-size:34px">Past Midlife</span>
      <span class="c-forest" style="font-size:30px">Zero Gym</span>
      <span class="c-forest" style="font-size:38px">Needed</span>
    </div>
  </section>

  <!-- Studio habits: photo with lower panel -->
  <section class="tile col-2 row-2">
    <div class="photo photo-friends" role="img" aria-label="Two women sharing a whispered secret, one looking delighted"></div>
    <div class="panel" style="left:0;top:170px;width:295px;height:198px;background:linear-gradient(180deg,rgba(46,74,72,0) 0%,var(--forest) 24%)"></div>
    <div class="stack center" style="left:0;top:196px;width:295px">
      <span class="c-rose" style="font-size:28px">Studio Habits</span>
      <span class="c-blush" style="font-size:27px">For Lasting Energy</span>
      <span class="c-blush" style="font-size:44px">Past Midlife</span>
      <span class="c-blush" style="font-size:23px">Zero Gym Needed</span>
    </div>
  </section>

  <!-- Studio habits: photo with side panel -->
  <section class="tile col-3 row-2">
    <div class="photo photo-sky" role="img" aria-label="Excited woman against a light blue wall with a friend behind her"></div>
    <div class="panel" style="left:120px;top:32px;width:175px;height:284px;background:var(--forest-glass)"></div>
    <div class="stack center" style="left:120px;top:44px;width:175px">
      <span class="c-rose" style="font-size:38px">Studio</span>
      <span class="c-rose" style="font-size:38px">Habits</span>
      <span class="c-blush" style="font-size:30px">For Lasting</span>
      <span class="c-blush" style="font-size:30px">Energy</span>
      <span class="c-blush" style="font-size:28px">Past Midlife</span>
      <span class="c-blush" style="font-size:22px">Zero Gym</span>
      <span class="c-blush" style="font-size:28px">Needed</span>
    </div>
  </section>

  <!-- Morning reboot: type only -->
  <section class="tile col-1 row-3 bg-gradient">
    <div class="stack center" style="left:0;top:40px;width:295px">
      <span class="c-forest" style="font-size:56px">Ten-Week</span>
      <span class="c-forest" style="font-size:80px;line-height:1.05">Bright</span>
      <span class="c-blush" style="font-size:46px">Morning</span>
      <span class="c-blush script" style="font-size:58px">Reboot</span>
    </div>
  </section>

  <!-- Morning reboot: cut-out portrait -->
  <section class="tile col-2 row-3 bg-soft">
    <div class="stack center" style="left:0;top:22px;width:295px">
      <span class="c-forest" style="font-size:36px">Ten-Week Bright</span>
      <span class="c-rose" style="font-size:40px">Morning</span>
      <span class="c-rose script" style="font-size:40px">Reboot</span>
    </div>
    <div class="figure" role="img" aria-label="Smiling woman in a white cropped sweater pointing at her waist" style="left:70px;top:210px;width:155px;height:158px"></div>
  </section>

  <!-- Morning reboot: kitchen portrait -->
  <section class="tile col-3 row-3">
    <div class="photo photo-kitchen" role="img" aria-label="Smiling woman in a white sweater standing in a kitchen, pointing down"></div>
    <div class="panel" style="left:82px;top:208px;width:130px;height:160px;background:linear-gradient(180deg,rgba(232,150,176,0) 0%,var(--rose) 30%)"></div>
    <div class="stack center" style="left:82px;top:222px;width:130px">
      <span class="c-forest" style="font-size:27px">Ten-Week</span>
      <span class="c-forest" style="font-size:42px">Bright</span>
      <span class="c-blush" style="font-size:25px">Morning</span>
      <span class="c-blush" style="font-size:26px">Reboot</span>
    </div>
  </section>

</main>
</body>
</html>
```